Real Estate Company
Residential & Commercial
Sales & Property Management

would like to use the logo i uploaded but would really love a black back ground...I think with the gold fleur dis lis and the maroon lettering it would really look great!

Industry/Entity Type

Business

Contact Information for Business Card

Our Coastal Real Estate Co.
Danielle Forbis
Broker/Owner
337-284-6093 Cell
337-726-0348 Office
8142 Willet Rd Bayou Crest LA 70583

```html
<!DOCTYPE html>
<html lang="en">
<head>
<meta charset="utf-8">
<title>Our Coastal Real Estate Co. — Business Card</title>
<link rel="stylesheet" href="https://fonts.googleapis.com/css2?family=Arimo:wght@400&display=swap">
<style>
  :root {
    --page: #ffffff;
    --frame: #4b4b4c;
    --card: #060708;
    --gold: #e8dc8f;
    --white: #ffffff;
  }
  html, body {
    margin: 0;
    padding: 0;
    width: 960px;
    height: 1200px;
    overflow: hidden;
    background: var(--page);
  }
  .card {
    position: absolute;
    left: 240px;
    top: 180px;
    width: 480px;
    height: 838px;
    background: var(--frame);
    overflow: hidden;
    font-family: "Arimo", Arial, sans-serif;
  }
  .card-face {
    position: absolute;
    inset: 24px;
    background: var(--card);
    border-radius: 14px;
    box-shadow: 0 0 16px 10px var(--card);
  }
  .brand {
    position: absolute;
    left: 0;
    right: 0;
    top: 178px;
    text-align: center;
    color: var(--gold);
    font-size: 40px;
    line-height: 48px;
    letter-spacing: 0.5px;
  }
  .contact {
    position: absolute;
    left: 0;
    right: 0;
    top: 392px;
    text-align: center;
    color: var(--white);
  }
  .contact-name {
    margin: 0;
    color: var(--gold);
    font-size: 35px;
    line-height: 44px;
    letter-spacing: 0.5px;
    font-weight: 400;
  }
  .contact-title {
    margin: 0 0 40px;
    font-size: 28px;
    line-height: 36px;
  }
  .contact-lines {
    margin: 0;
    font-style: normal;
    font-size: 30.5px;
    line-height: 40px;
    letter-spacing: 0.8px;
  }
</style>
</head>
<body>
  <div class="card">
    <div class="card-face">
      <div class="brand">Our Coastal<br>Real Estate Co.</div>
      <div class="contact">
        <h1 class="contact-name">Danielle Forbis</h1>
        <p class="contact-title">Broker/Owner</p>
        <address class="contact-lines">
          337.284.6093 Cell<br>
          337.726.0348 Office<br>
          8142 Willet Rd.<br>
          Bayou Crest LA 70583
        </address>
      </div>
    </div>
  </div>
</body>
</html>
```